Ward Compass Business Card Design*

We need a business card design for our company Ward Compass. Our company is specialized in providing online consulting services regarding medical institutions, hospitals and doctors. We work with patients worldwide looking to choose between healthcare providers. We have a website you may use as a reference, where we list doctors and clinics worldwide. So we target Medical providers as well as patients worldwide.
Target Market(s)
Medical Providers and patients around the world
Industry/Entity Type
Medical
Contact Information for Business Card
Salwa Kettani
CEO
+90 612 348 2175
info@wardcompass.example
www.wardcompass.example
14 Annakhil 7 H.R.B. Rabat, Morocco
Requirements
Must have
- Company logo/name on one full side, personal info and smaller logo and company name on the other side.
Nice to have
- Smart and elegant design

```html
<!DOCTYPE html>
<html lang="en">
<head>
<meta charset="utf-8">
<title>Ward Compass Business Card</title>
<link rel="stylesheet" href="https://fonts.googleapis.com/css2?family=Lato:wght@400;700&display=swap">
<style>
  :root {
    --bg: #e9e6e1;
    --card-top: #36a8db;
    --card-bottom: #2f76b6;
    --white: #ffffff;
    --brand: #2f7fc1;
    --shadow: rgba(0, 0, 0, 0.35);
  }
  * { margin: 0; padding: 0; box-sizing: border-box; }
  html, body { width: 1200px; height: 900px; overflow: hidden; }
  body {
    position: relative;
    background: var(--bg);
    font-family: "Lato", sans-serif;
  }
  .card {
    position: absolute;
    width: 556px;
    height: 344px;
    box-shadow: 3px 4px 6px var(--shadow);
  }
  .card-front {
    left: 330px; top: 90px;
    background: linear-gradient(to bottom, var(--card-top), var(--card-bottom));
    color: var(--white);
    text-align: center;
  }
  .card-back {
    left: 330px; top: 469px;
    width: 559px;
    background: var(--white);
  }
  .person-name {
    position: absolute; left: 0; right: 0; top: 98px;
    font-size: 20px; letter-spacing: 0.2px; font-weight: 400;
  }
  .person-name strong { font-weight: 700; }
  .person-role {
    position: absolute; left: 0; right: 0; top: 122px;
    font-size: 15px;
  }
  .contact-divider {
    position: absolute; left: 187px; top: 148px;
  }
  .contact-list {
    position: absolute; left: 0; right: 0; top: 184px;
    list-style: none; font-size: 15.5px; line-height: 20.5px;
  }
  .brand-lockup {
    position: absolute; left: 0; right: 0; top: 148px;
    display: flex; align-items: center; justify-content: center; gap: 14px;
  }
  .brand-dot {
    width: 46px; height: 46px; border-radius: 50%;
    background: var(--brand);
  }
  .brand-name {
    font-size: 29px; font-weight: 700; letter-spacing: 0.5px;
    color: var(--brand); text-transform: uppercase;
  }
</style>
</head>
<body>
  <section class="card card-front">
    <p class="person-name"><strong>SALWA</strong> KETTANI</p>
    <p class="person-role">CEO</p>
    <svg class="contact-divider" width="180" height="30" viewBox="0 0 180 30" aria-hidden="true">
      <g stroke="#ffffff" stroke-width="1.2" fill="none">
        <line x1="0" y1="15" x2="50" y2="15"/>
        <line x1="130" y1="15" x2="180" y2="15"/>
      </g>
      <g fill="#ffffff">
        <circle cx="63" cy="15" r="11"/>
        <circle cx="90" cy="15" r="11"/>
        <circle cx="117" cy="15" r="11"/>
      </g>
      <g fill="#3290c9" stroke="#3290c9">
        <path d="M57 12 q6 -5 12 0 v2 h-3 v-1.5 h-6 v1.5 h-3z" stroke-width="0.5"/>
        <rect x="58.5" y="15" width="9" height="5" rx="1" stroke="none"/>
        <rect x="84" y="10.5" width="12" height="9" fill="none" stroke-width="1.4"/>
        <polyline points="84,10.5 90,16 96,10.5" fill="none" stroke-width="1.4"/>
        <circle cx="117" cy="15" r="6" fill="none" stroke-width="1.4"/>
        <path d="M114 11 q3 2 1 5 q3 1 2 4 M119 10 q-1 3 2 4" fill="none" stroke-width="1.3"/>
      </g>
    </svg>
    <ul class="contact-list">
      <li>+90 612 348 2175</li>
      <li>info@wardcompass.example</li>
      <li>www.wardcompass.example</li>
    </ul>
  </section>

  <section class="card card-back">
    <div class="brand-lockup">
      <span class="brand-dot" aria-hidden="true"></span>
      <span class="brand-name">Ward Compass</span>
    </div>
  </section>
</body>
</html>
```